TrailPeakMotion-fitness app follows the owner or client moves, let them monitor their weight & fitness

TrailPeakMotion -fitness app, the avatar changes & evolve with the data logged in. the avatar resembles the client. the avatar weight looks like the client. When the client loses weight or gains weight, the avatar changes.
A brief is attached, check it out and get back to me with you're design.

Every week I will increase by 100€ instead.

Trailpeakmotion -fitness App Idea.
Two Business Logo.

March 2013 Ireland, the land of magic. Trailpeakmotion was born. Copy the client moves. With the avatar.
The app is about fitness, I have a vision and that you can be part of it.
Let's change the world together!
- the 1st page is about trailpeakmotion mission/founder/value of the company.
I will attach all information on Page(A)
after the intro, Terms and conditions poly/data policy ( the client has to agree and Sign before continuing. Then comes the page ParQ
the ParQ is a questionnaire asking the client to know more about them!
ParQ features the beginning: Create your personalized Avatar ( change clothes – if they choose no cloths, by default the avatar will have a pair of short- pant/hair/ eyes colour/ and select Body type: Ectomorph/ endomorph/ mesomorph or the client can select a mix body type.
Age select/ currant weight/ desired weight/ skin colour/ gender: male, female, Transgender, other.
Fitness goals: what the client desire how they are going to achieve it/ the measure they will take to achieve it or I don’t know option. The press continues / the app analyses all the data and create their personalise unique Avatar. That will look like the description they provided.
Page 2nd feature: they will see their full-body avatar.
Next, the client needs to continue completing more information.
Stress level select/ nutrition habits select/ and nutrition habit desired select/ injuries select/ allergies select/ history of any health complication question to answer/ Gp ( their Doctor name and number, to fill in/ and a person to contact in case of an emergency. Fill-in answer).
Page 3rd The Main Page. This results will depend on the answer of E-Wallet (5)
TrailPeakMotion-fitness Pro APP, Will analyse all the data and the app will suggest the best fitness program, nutrition plan, meditation advice to help them with stress/ and sleep hours they need to recover from after exercise/ base on their body type, fitness goal, and current stress level.
Main page Features: Keep in mind; the avatar changes form constantly, all depend on the information the client put on the profile setting.
1- the Avatar
- the can look Happy
- or sad – the reason why! Can tell the client all the reason for being that way and the solutions to make it better.
- Angry- Reason why! Can tell the client all the reason for being that way and the solutions to make it better.
- if the client gain weight, it will show on the avatar body.
- When the client loses weight the avatar will tell the client with a notification and it shows o the avatar body.
2- fitness check the app call Trenola and Stridewell fitness app, I like their page layout, it might show you what type of page I’m looking for and the quality that hoping or expecting.
- Muscle 3d full body when selecting a muscle it will show you the best exercises to work that particular muscle and weight recommendation. Check the app called
- Fitness Equipment to target each muscle and best suggestion for each muscle.
- Exercises all exercise available to get someone I top shape and the option to add more custom exercises. Liked exercise option/ search for exercises option/ reminder option.
- Nutrition Plans ( Vegan option/ paleo diet Option/ Keto diet/ build their own pers meal plan.
- Wellness Suggestions, tips raising your energy level
3- social Media
- Pictoria
- ChatLoop
- Boardly
- Kinnora
Feedback option
4- Music
- connect to Tunevault.
- Connect to playlist Custom
- Connect to Melodro
5- E-wallet
- buy a 1to1 personal training session ( only for members living in the country as
the founder)
- Buy 1 sessions/ 45Minutes 45€
- Buy 1sessions / 30 Minutes 35€
- Buy 1 session / 60 Minutes 55€
App subscription ( 2 options)
- Buy one Month subscription 7.99€ app
- Buy one Year Subscription for 107.88€ Share it with 10 people for the best deal 49.99€ for 12 months.
6- share it
on any social platform on the list
7- Picture Gallery
- before Pic
- after pic
8 – Deals & Offers
link to affiliated with other organization( trailpeakmotion will put all fitness deals and offers on this page.
9 –Contacts
- Gps number and information
-- Friend or family to contact during an emergency
10- Testimonials
- Reviews
11- To-do List
- Calendar bookings
- fitness goal planner
12- Chat On The app community
- a page where all the app members can chat if they open the portal and agree to it.
13- Profile settings
- account settings
14-Progress Tracker
15 – Connect Fit Device
-- Progression CHART.
- Junk food / sweet tracker (obviously the client need to log in what they eat each time.
Base on what they eat the Avatar will take shape/ increase weight or lose weight / change mood/ the client will know when they are doing something wrong or right base on how the avatar mood.
I this idea is yours to be part of something different, this idea is will donate for young and family who need help and support.

WELCOME TO TrailPeakMotion-fitness Private Studio
OUR MISSION
TrailPeakMotion an Ireland based company whose mission is to help you
complete your journey stronger, faster with confidence.
ABOUT TRAILPEAKMOTION
TrailPeakMotion-fitness Was created from and inspire by the Irish strength and power to conquer any challenges, in 2013 after winning a boxing tournament in the national stadium. Driven by the desire to make a difference in the sports industry, I won that knight because my hunger for success was bigger than my opponents. TrailPeakMotion-fitness Private Studio, I decided to teach and coach people, how to improve their fitness components with all the experience I have under my belt. My Mission is to inspire and be inspired by the new young talents in need for an opportunity.
TrailPeakMotion-fitness Private Studio – Your energy is what keeps us moving and striving for a better and stronger united community. Fitness is the future & wellness is life.
I. OUR FOUNDER
Born and raised in the Caribbean, I started boxing when I was 19 years of age.
I started fighting to learn how to defend myself from bullying and protect my mother.
I started winning all my amateur fights, travelling around the world, the idea of travelling and the famous side of being a fighter kind started to like a little bit. My ambition didn’t stop there, it grew to aim for the stars and bigger plans.
I always dreamed of owning my own cloth brand and my own fitness gym. All over the Caribbean.
My peaceful Land (Dominican Rep, gave me the qualities to rise and achieve many goals. I believe- everything and anything is possible, once you have the right mindset and dedication to achieve it.
Trained by many of the best in coach in Ireland.
Now is time to share my knowledge.
OUR VALUES:
We value top quality Service and will ensure you have an amazing experience with TrailPeakMotion Fitness. If not, write to us and we’ll make it right.
II. GIVING BACK:
To help and support those in need in our communities.
10% of our earning will be used to help and support people in need in the Dominican Republic, Haiti and all the Caribbean. We support our young athletes with big dreams. Seeing them succeed is the best gift the world can give us all.
Good Luck to all who will take this challenge. Remember this is only the start, the winner will gain an extra bonus for completing this work. And the chance to continue working with us.
III. You Can check the app call fitness Duo or stridewell a fitness app
these fitness features and setting is the style and standard I am looking for.

Target Market(s)

Fitness/ Nutrition & well Being

Contact Information for Business Card

Trailpeakmotion@quillpost.example
0871234567
www.trailpeakmotionfitness.example
The logo is on my brief.
On the card, I want trailPeakMotion Fitness Pro.
I like an attractive colour like gold champagne on the main front side and on the back I want black and green to match the logo. sharp and professional style.

Font styles to use
Serif
Decorative
Script

Requirements
Must have
• Most have an option to create an avatar, to look like the client profile and weight/ hairstyle. This session is for the (App) https://vidshare.example/Qw82ZxPlmN
Ectomorph body type.
Endomorph body type.
mesomorph body type.
or a mix body type option.
base on the body type the client will be suggested by the trailpeakmotion the best plan for them.
Most have a challenges page: like squat challenge/ push-Ups challenge/ few fitness challenges to motivate the client.
Nice to have
• I would like to have every single muscle on the human body with all the exercises to work that particular muscle. like fitness duo or stride Well fitness app
Must have a progression chart, to show the client his/her fitness progression on their: strength/ speed/ push-ups/ flexibility/ Cardio or their V02 Max.
also, Fitness test option; every month or even every the client wishes the can test their fitness.

I found an Idea on the net: https://vidshare.example/Qw82ZxPlmN
Thank you, a step closer to a better world.

```html
<!DOCTYPE html>
<html lang="en">
<head>
<meta charset="utf-8">
<title>TrailPeakMotion – App Screens</title>
<link rel="stylesheet" href="https://fonts.googleapis.com/css2?family=IBM+Plex+Sans:wght@400;600;700&family=Playfair+Display:wght@500&display=swap">
<style>
  :root {
    --stage: #96979b;
    --screen: #f6f5f3;
    --bar: #ffffff;
    --ink: #111111;
    --text: #2a2a2a;
    --star: #f0562a;
    --star-muted: #b8bccb;
    --pictoria: #3a7fa8;
    --chatloop: #12bd1a;
    --boardly: #c40008;
    --kinnora: #3c53a0;
    --card: #ffffff;
  }
  * { box-sizing: border-box; margin: 0; padding: 0; }
  html, body { width: 1200px; height: 708px; overflow: hidden; }
  body {
    background: var(--stage);
    font-family: "IBM Plex Sans", Arial, sans-serif;
    color: var(--ink);
    position: relative;
  }
  .screen {
    position: absolute;
    top: 58px;
    width: 331px;
    height: 589px;
    background: var(--screen);
    overflow: hidden;
  }
  .screen--social { left: 55px; }
  .screen--reviews { left: 419px; }
  .screen--gallery { left: 792px; }

  .app-bar {
    height: 48px;
    background: var(--bar);
    display: flex;
    align-items: center;
    justify-content: center;
    box-shadow: 0 1px 2px rgba(0,0,0,0.06);
  }
  .brand {
    font-family: "Playfair Display", Georgia, serif;
    font-weight: 500;
    font-size: 15px;
    letter-spacing: 0.5px;
    color: var(--ink);
  }
  .screen-title {
    position: absolute;
    left: 0; right: 0;
    text-align: center;
    font-weight: 700;
    font-size: 16.5px;
    letter-spacing: 0.6px;
  }
  .screen--social .screen-title { top: 76px; }
  .screen--reviews .screen-title, .screen--gallery .screen-title { top: 72px; }

  /* Social */
  .network {
    position: absolute;
    left: 50px;
    width: 233px;
    height: 42px;
    display: flex;
    align-items: center;
    padding-left: 14px;
    color: #fff;
    font-weight: 700;
    font-size: 15px;
    letter-spacing: 0.5px;
  }
  .network__dot {
    width: 20px; height: 20px;
    border-radius: 50%;
    border: 2px solid #fff;
    margin-right: 16px;
    flex: none;
  }
  .network--pictoria { top: 133px; background: var(--pictoria); }
  .network--chatloop { top: 190px; background: var(--chatloop); }
  .network--boardly { top: 245px; background: var(--boardly); }
  .network--kinnora { top: 300px; background: var(--kinnora); }

  .feedback {
    position: absolute;
    left: 50px; top: 342px;
    width: 233px; height: 186px;
    background: var(--kinnora);
    padding: 17px 19px 0;
  }
  .feedback__stars { display: flex; gap: 5px; }
  .feedback__comment {
    margin-top: 16px;
    width: 197px; height: 74px;
    background: #fff;
    padding: 12px 12px;
    font-size: 10px;
    font-weight: 600;
    color: #444;
    letter-spacing: 0.3px;
  }
  .feedback__submit {
    display: inline-block;
    margin-top: 14px;
    width: 74px; height: 26px;
    background: #fff;
    color: var(--kinnora);
    font-weight: 700;
    font-size: 12.5px;
    text-align: center;
    line-height: 26px;
    letter-spacing: 0.4px;
  }

  /* Reviews */
  .review {
    position: absolute;
    left: 15px;
    width: 302px; height: 127px;
    background: var(--card);
    box-shadow: 0 1px 3px rgba(0,0,0,0.06);
    padding: 17px 21px 0;
  }
  .review:nth-of-type(1) { top: 112px; }
  .review:nth-of-type(2) { top: 251px; }
  .review:nth-of-type(3) { top: 391px; }
  .review:nth-of-type(4) { top: 529px; }
  .review__stars { display: flex; gap: 2px; height: 10px; }
  .review__text {
    margin-top: 7px;
    font-size: 11px;
    line-height: 14.4px;
    color: var(--text);
  }
  .review__author {
    margin-top: 9px;
    display: flex;
    align-items: center;
  }
  .review__avatar {
    width: 26px; height: 26px;
    border-radius: 50%;
    background: linear-gradient(135deg, #c9cdd4, #7d8594);
    margin-right: 8px;
    flex: none;
  }
  .review__name { font-size: 10px; font-weight: 700; line-height: 11px; }
  .review__place { font-size: 10px; line-height: 11px; color: var(--text); }

  /* Gallery */
  .gallery {
    position: absolute;
    left: 10px; top: 117px;
    display: grid;
    grid-template-columns: 151px 151px;
    grid-auto-rows: 110px;
    column-gap: 8px;
    row-gap: 7px;
  }
  .gallery__photo { width: 151px; height: 110px; }
  .tone-dark { background: linear-gradient(90deg, #1a1d22, #6b5648 50%, #1a1d22); }
  .tone-light { background: linear-gradient(90deg, #eeeef2, #c99a7e 50%, #eeeef2); }
  .tone-deep { background: linear-gradient(90deg, #9a9a9c, #5b3a2a 50%, #9a9a9c); }
  .tone-back { background: linear-gradient(90deg, #efeff3, #c79d84 50%, #efeff3); }
  .tone-pale { background: linear-gradient(90deg, #e4e4e8, #efd9cc 50%, #e4e4e8); }
  .tone-grey { background: linear-gradient(90deg, #8d8d8f, #c8a488 50%, #8d8d8f); }
  .tone-night { background: linear-gradient(90deg, #0c0c0e, #b89482 50%, #0c0c0e); }
  .tone-gold { background: linear-gradient(90deg, #0c0c0e, #d6b07d 50%, #0c0c0e); }
</style>
</head>
<body>
  <svg width="0" height="0" style="position:absolute">
    <defs>
      <polygon id="star" points="10,1 12.6,7.2 19.3,7.6 14.1,11.8 15.8,18.4 10,14.8 4.2,18.4 5.9,11.8 0.7,7.6 7.4,7.2"/>
    </defs>
  </svg>

  <section class="screen screen--social">
    <header class="app-bar"><span class="brand">TRAILPEAKMOTION</span></header>
    <h2 class="screen-title">SOCIAL MEDIA</h2>
    <div class="network network--pictoria"><span class="network__dot"></span>PICTORIA</div>
    <div class="network network--chatloop"><span class="network__dot"></span>CHATLOOP</div>
    <div class="network network--boardly"><span class="network__dot"></span>BOARDLY</div>
    <div class="network network--kinnora"><span class="network__dot"></span>KINNORA</div>
    <div class="feedback">
      <div class="feedback__stars">
        <svg width="18" height="18" viewBox="0 0 20 20"><use href="#star" fill="var(--star-muted)"/></svg>
        <svg width="18" height="18" viewBox="0 0 20 20"><use href="#star" fill="var(--star-muted)"/></svg>
        <svg width="18" height="18" viewBox="0 0 20 20"><use href="#star" fill="var(--star-muted)"/></svg>
        <svg width="18" height="18" viewBox="0 0 20 20"><use href="#star" fill="var(--star-muted)"/></svg>
        <svg width="18" height="18" viewBox="0 0 20 20"><use href="#star" fill="var(--star-muted)"/></svg>
      </div>
      <div class="feedback__comment">WRITE COMMENT</div>
      <div class="feedback__submit">SUBMIT</div>
    </div>
  </section>

  <section class="screen screen--reviews">
    <header class="app-bar"><span class="brand">TRAILPEAKMOTION</span></header>
    <h2 class="screen-title">REVIEWS</h2>
    <article class="review">
      <div class="review__stars">
        <svg width="10" height="10" viewBox="0 0 20 20"><use href="#star" fill="var(--star)"/></svg><svg width="10" height="10" viewBox="0 0 20 20"><use href="#star" fill="var(--star)"/></svg><svg width="10" height="10" viewBox="0 0 20 20"><use href="#star" fill="var(--star)"/></svg><svg width="10" height="10" viewBox="0 0 20 20"><use href="#star" fill="var(--star)"/></svg><svg width="10" height="10" viewBox="0 0 20 20"><use href="#star" fill="var(--star)"/></svg>
      </div>
      <p class="review__text">Sed ut perspiciatis unde omnis iste natus err or sit voluptatem accusantium dolore mqu e lauda ntium totam rem aperiam eaque ipsa quae.</p>
      <div class="review__author"><span class="review__avatar" role="img" aria-label="Reviewer portrait"></span><div><div class="review__name">RICHARD</div><div class="review__place">England</div></div></div>
    </article>
    <article class="review">
      <div class="review__stars">
        <svg width="10" height="10" viewBox="0 0 20 20"><use href="#star" fill="var(--star)"/></svg><svg width="10" height="10" viewBox="0 0 20 20"><use href="#star" fill="var(--star)"/></svg><svg width="10" height="10" viewBox="0 0 20 20"><use href="#star" fill="var(--star)"/></svg><svg width="10" height="10" viewBox="0 0 20 20"><use href="#star" fill="var(--star)"/></svg><svg width="10" height="10" viewBox="0 0 20 20"><use href="#star" fill="var(--star)"/></svg>
      </div>
      <p class="review__text">Sed ut perspiciatis unde omnis iste natus err or sit voluptatem accusantium dolore mqu e lauda ntium totam rem aperiam eaque ipsa quae.</p>
      <div class="review__author"><span class="review__avatar" role="img" aria-label="Reviewer portrait"></span><div><div class="review__name">RICHARD</div><div class="review__place">England</div></div></div>
    </article>
    <article class="review">
      <div class="review__stars">
        <svg width="10" height="10" viewBox="0 0 20 20"><use href="#star" fill="var(--star)"/></svg><svg width="10" height="10" viewBox="0 0 20 20"><use href="#star" fill="var(--star)"/></svg><svg width="10" height="10" viewBox="0 0 20 20"><use href="#star" fill="var(--star)"/></svg><svg width="10" height="10" viewBox="0 0 20 20"><use href="#star" fill="var(--star)"/></svg><svg width="10" height="10" viewBox="0 0 20 20"><use href="#star" fill="var(--star)"/></svg>
      </div>
      <p class="review__text">Sed ut perspiciatis unde omnis iste natus err or sit voluptatem accusantium dolore mqu e lauda ntium totam rem aperiam eaque ipsa quae.</p>
      <div class="review__author"><span class="review__avatar" role="img" aria-label="Reviewer portrait"></span><div><div class="review__name">RICHARD</div><div class="review__place">England</div></div></div>
    </article>
    <article class="review">
      <div class="review__stars">
        <svg width="10" height="10" viewBox="0 0 20 20"><use href="#star" fill="var(--star)"/></svg><svg width="10" height="10" viewBox="0 0 20 20"><use href="#star" fill="var(--star)"/></svg><svg width="10" height="10" viewBox="0 0 20 20"><use href="#star" fill="var(--star)"/></svg><svg width="10" height="10" viewBox="0 0 20 20"><use href="#star" fill="var(--star)"/></svg><svg width="10" height="10" viewBox="0 0 20 20"><use href="#star" fill="var(--star)"/></svg>
      </div>
      <p class="review__text">Sed ut perspiciatis unde omnis iste natus err or sit voluptatem accusantium dolore mqu e lauda ntium totam rem aperiam eaque ipsa quae.</p>
    </article>
  </section>

  <section class="screen screen--gallery">
    <header class="app-bar"><span class="brand">TRAILPEAKMOTION</span></header>
    <h2 class="screen-title">PHOTO GALLERY</h2>
    <div class="gallery">
      <div class="gallery__photo tone-dark" role="img" aria-label="Before and after avatar, female body in swimwear on dark background"></div>
      <div class="gallery__photo tone-light" role="img" aria-label="Before and after avatar, male torso front view"></div>
      <div class="gallery__photo tone-deep" role="img" aria-label="Before and after avatar, male torso on grey background"></div>
      <div class="gallery__photo tone-back" role="img" aria-label="Before and after avatar, male back view"></div>
      <div class="gallery__photo tone-pale" role="img" aria-label="Before and after avatar, female body in white swimwear"></div>
      <div class="gallery__photo tone-grey" role="img" aria-label="Before and after avatar, male body front view"></div>
      <div class="gallery__photo tone-night" role="img" aria-label="Avatar front and back view, female body on black background"></div>
      <div class="gallery__photo tone-gold" role="img" aria-label="Before and after avatar, female body on black background"></div>
    </div>
  </section>
</body>
</html>
```